Wrenfield Pharmacy opening

We want to have a double sided 5.5"x8.5" flyer for a new Pharmacy opening in a well known strip mall in the neighborhood and we are planning to mail it to neighbors homes.

Want to put the outside pharmacy picture on the main side of the flyer and a coupon with 25% off towards an OTC product on the back in addition to the info below (preferably in a sort of bulletin points not a list (something like the 2 examples attached).

Colors to be red like the exterior sign and blue like the interior wall paint:

Front side should have:
Wrenfield pharmacy
Your locally owned and operated pharmacy around the corner.
317-4821 Ostrander rd.
Pike hollow plaza
T. 555 206 3379 (call or text)
F. 555-206-3381

Free prescription delivery
Text us for refills
Specialized compounding
Customized compression stockings

The back side should have:

Do you forget taking your medications! We offer multiple compliance packaging options at no additional cost.
Had shingles before or worried to have it? travelling soon? check our vaccinations options!
Suffering side effects? We are experienced to check your medications interactions & different coverage options.
Hard time monitoring your blood pressure? Trying to stop smoking? we can always help.

FEELING BETTER STARTS HERE

```html
<!DOCTYPE html>
<html lang="en">
<head>
<meta charset="utf-8">
<title>Wrenfield Pharmacy – Opening Flyer</title>
<link rel="stylesheet" href="https://fonts.googleapis.com/css2?family=Rubik:wght@400;500;700&family=Oswald:wght@400;500&display=swap">
<style>
  :root{
    --red:#e8000b;
    --red-dark:#c4000a;
    --ink:#1d1d1d;
    --footer:#333335;
    --white:#ffffff;
    --stage:#d6d6d6;
    --mint:#e6f0df;
    --sky:#a9cbe9;
    --facade:#8e8378;
    --glass:#4b4f58;
    --wall-blue:#465a97;
    --ceiling:#eeece6;
    --shelf:#d8cfc2;
    --leaf:#9fd46f;
  }
  *{box-sizing:border-box;margin:0;padding:0}
  html,body{width:1200px;height:904px;overflow:hidden}
  body{background:var(--stage);font-family:"Rubik",Arial,sans-serif;position:relative;color:var(--ink)}

  .flyer{position:absolute;top:156px;width:457px;height:706px;overflow:hidden;background:var(--white)}
  .flyer--front{left:44px}
  .flyer--back{left:556px;background:linear-gradient(180deg,#fff 0%,#f3f6ef 55%,var(--mint) 100%)}

  .brand{position:absolute;left:20px;top:18px;display:flex;align-items:center;gap:8px;z-index:3}
  .brand__name{font-weight:500;color:var(--red);font-size:21px;line-height:21px;letter-spacing:.3px}
  .brand__dot{width:50px;height:50px;border-radius:50%;background:var(--red)}

  .photo{position:absolute;left:0;top:0;width:100%}
  .photo--storefront{height:378px;background:linear-gradient(180deg,var(--sky) 0%,#cfe0ef 15%,#7d736a 24%,var(--facade) 50%,var(--glass) 62%,#5a5a5e 92%,#6a6560 100%)}
  .photo--interior{height:400px;background:linear-gradient(180deg,var(--ceiling) 0%,#e4e2dc 24%,var(--wall-blue) 25%,var(--wall-blue) 44%,var(--shelf) 45%,#e9e4dc 80%,rgba(233,240,228,0) 100%)}

  .bands{position:absolute;left:0;top:0;z-index:2}

  /* front lower section */
  .tagline{position:absolute;left:20px;top:382px;font-family:"Oswald",Arial,sans-serif;font-size:22px;line-height:27px;z-index:3}
  .tagline__red{color:var(--red);font-weight:500}
  .tagline__dark{color:var(--ink)}
  .mascots{position:absolute;left:10px;top:470px;width:218px;height:175px;background:radial-gradient(ellipse at 50% 45%,#fbe9e8 0%,#f4f4f6 55%,#fff 100%);z-index:1}

  .services{position:absolute;left:227px;top:373px;width:209px;height:295px;background:var(--red);border-radius:0 0 10px 10px;padding:10px 0 0 13px;z-index:3}
  .service{display:flex;align-items:center;height:69px;gap:15px}
  .service__icon{width:58px;height:58px;border-radius:50%;background:var(--white);flex:none;display:flex;align-items:center;justify-content:center}
  .service__label{color:var(--white);font-weight:500;font-size:15.5px;line-height:19.5px}

  .footer{position:absolute;left:0;bottom:0;width:100%;height:52px;display:flex;align-items:center;justify-content:space-between;padding:6px 20px 0 20px;color:var(--white);font-size:11.5px;line-height:14px;z-index:4}
  .contact{display:flex;align-items:center;gap:5px}
  .contact svg{flex:none}

  /* back text */
  .copy{position:absolute;left:20px;top:354px;width:245px;z-index:3;font-size:11px;line-height:14px}
  .copy__lead{font-size:21.5px;line-height:26px;font-weight:500;color:var(--ink)}
  .copy__headline{font-size:21.5px;line-height:28px;font-weight:700;color:var(--red);margin-bottom:2px}
  .copy p{margin-bottom:2px}
  .copy .gap{margin-top:9px}
  .accent{color:var(--red);font-weight:500}
  .copy b{font-weight:500}
  .copy__help{color:var(--red);font-weight:700;font-size:12.5px;margin-top:6px}
  .slogan{margin-top:10px;font-size:15.5px;line-height:19px;font-weight:700}
  .slogan__red{color:var(--red)}
  .growth{position:absolute;left:262px;top:392px;width:190px;height:150px;background:radial-gradient(ellipse at 55% 55%,var(--leaf) 0%,#c7e6a8 40%,rgba(230,240,223,0) 75%);z-index:2}

  .coupon{position:absolute;left:272px;top:548px;width:166px;height:70px;background:var(--white);border:2px dashed var(--red);border-radius:6px;z-index:3;text-align:center;padding-top:6px}
  .coupon__value{font-size:22px;line-height:24px;font-weight:700;color:var(--red)}
  .coupon__item{font-size:10.5px;line-height:13px;font-weight:500;color:var(--ink)}
  .coupon__terms{font-size:8px;line-height:11px;color:#555}
</style>
</head>
<body>

<!-- FRONT -->
<section class="flyer flyer--front">
  <div class="photo photo--storefront" role="img" aria-label="Photo of the pharmacy storefront in the plaza with its red exterior sign"></div>

  <svg class="bands" width="457" height="706" viewBox="0 0 457 706" aria-hidden="true">
    <polygon points="0,100 457,42 457,56 0,110" fill="var(--red)"/>
    <polygon points="0,378 457,378 457,706 0,706" fill="#fff"/>
    <polygon points="0,352 457,372 457,383 0,366" fill="var(--red)"/>
    <polygon points="0,360 457,376 457,390 0,378" fill="#fff"/>
    <polygon points="0,655 457,632 457,706 0,706" fill="var(--footer)"/>
    <polygon points="0,648 457,626 457,632 0,655" fill="var(--red)"/>
  </svg>

  <div class="brand">
    <div class="brand__name">WRENFIELD<br>PHARMACY</div>
    <div class="brand__dot"></div>
  </div>

  <div class="tagline">
    <div class="tagline__red">YOUR LOCALLY OWNED</div>
    <div class="tagline__dark">and operated pharmacy</div>
    <div class="tagline__red">around the corner.</div>
  </div>

  <div class="mascots" role="img" aria-label="Illustration of friendly pill characters"></div>

  <div class="services">
    <div class="service">
      <div class="service__icon">
        <svg width="36" height="28" viewBox="0 0 36 28" fill="none" stroke="#e8000b" stroke-width="2"><rect x="2" y="6" width="20" height="14" rx="1"/><path d="M22 10h7l5 5v5H22z"/><circle cx="9" cy="22" r="3" fill="#fff"/><circle cx="28" cy="22" r="3" fill="#fff"/></svg>
      </div>
      <div class="service__label">FREE<br>PRESCRIPTION<br>DELIVERY</div>
    </div>
    <div class="service">
      <div class="service__icon">
        <svg width="34" height="34" viewBox="0 0 34 34" fill="none" stroke="#e8000b" stroke-width="2"><path d="M6 17a11 11 0 0 1 19-7.5M28 17a11 11 0 0 1-19 7.5"/><path d="M25 4v6h-6M9 30v-6h6"/><rect x="11" y="13" width="12" height="8" rx="4" transform="rotate(-40 17 17)"/></svg>
      </div>
      <div class="service__label">Text us<br>for refills</div>
    </div>
    <div class="service">
      <div class="service__icon">
        <svg width="34" height="34" viewBox="0 0 34 34" fill="none" stroke="#e8000b" stroke-width="2"><polygon points="12,6 19,10 19,18 12,22 5,18 5,10"/><polygon points="22,14 29,18 29,26 22,30 15,26 15,18"/></svg>
      </div>
      <div class="service__label">Specialized<br>compounding</div>
    </div>
    <div class="service">
      <div class="service__icon">
        <svg width="30" height="34" viewBox="0 0 30 34" fill="none" stroke="#e8000b" stroke-width="2"><path d="M10 3h9v16l6 6v5H12l-4-6 2-5z"/><path d="M10 9h9M10 14h9"/></svg>
      </div>
      <div class="service__label">Customized<br>compression<br>stockings</div>
    </div>
  </div>

  <footer class="footer">
    <div class="contact">
      <svg width="13" height="13" viewBox="0 0 14 14" fill="none" stroke="#fff" stroke-width="1.2"><circle cx="7" cy="7" r="6"/><path d="M7 3.5a2 2 0 0 1 2 2c0 1.6-2 3.5-2 3.5S5 7.1 5 5.5a2 2 0 0 1 2-2z"/></svg>
      <span>317-4821 Ostrander rd.<br>Pike hollow plaza</span>
    </div>
    <div class="contact">
      <svg width="13" height="13" viewBox="0 0 14 14" fill="none" stroke="#fff" stroke-width="1.2"><circle cx="7" cy="7" r="6"/><path d="M4.5 4c.5 2.8 2.2 4.7 5 5.5l.8-1.2-1.5-.9-.6.6c-1-.5-1.7-1.2-2.2-2.2l.6-.6-.9-1.5z"/></svg>
      <span>555 206 3379 (call or text)</span>
    </div>
    <div class="contact">
      <svg width="13" height="13" viewBox="0 0 14 14" fill="none" stroke="#fff" stroke-width="1.2"><circle cx="7" cy="7" r="6"/><rect x="4" y="6" width="6" height="4"/><path d="M5 6V4h4v2"/></svg>
      <span>555-206-3381</span>
    </div>
  </footer>
</section>

<!-- BACK -->
<section class="flyer flyer--back">
  <div class="photo photo--interior" role="img" aria-label="Photo of the pharmacy interior with blue walls, counter and product shelves"></div>

  <svg class="bands" width="457" height="706" viewBox="0 0 457 706" aria-hidden="true">
    <polygon points="0,655 457,632 457,706 0,706" fill="var(--footer)"/>
    <polygon points="0,648 457,626 457,632 0,655" fill="var(--red)"/>
  </svg>

  <div class="brand">
    <div class="brand__name">WRENFIELD<br>PHARMACY</div>
    <div class="brand__dot"></div>
  </div>

  <div class="growth" role="img" aria-label="Illustration of green leaves growing from an open capsule with health icons"></div>

  <div class="coupon">
    <div class="coupon__value">25% OFF</div>
    <div class="coupon__item">any one OTC product</div>
    <div class="coupon__terms">Bring this coupon in store. One per visit.</div>
  </div>

  <div class="copy">
    <div class="copy__lead">Do you forget taking</div>
    <div class="copy__headline">YOUR MEDICATIONS!</div>
    <p><span class="accent">WE OFFER</span> multiple compliance packaging options at no additional cost.</p>
    <p><b>Had shingles before or worried to have it?</b><br>Travelling soon?<br>Check our vaccinations options!</p>
    <p class="gap"><span class="accent">Suffering side effects?</span><br>We are experienced to check your <b>medications interactions</b> &amp; <b>different coverage</b> options.</p>
    <p>Hard time monitoring your <b>blood pressure</b>?<br>Trying to <b>stop smoking</b>?</p>
    <div class="copy__help">WE CAN ALWAYS HELP.</div>
    <div class="slogan">FEELING BETTER<br><span class="slogan__red">STARTS HERE</span></div>
  </div>

  <footer class="footer">
    <div class="contact">
      <svg width="13" height="13" viewBox="0 0 14 14" fill="none" stroke="#fff" stroke-width="1.2"><circle cx="7" cy="7" r="6"/><path d="M7 3.5a2 2 0 0 1 2 2c0 1.6-2 3.5-2 3.5S5 7.1 5 5.5a2 2 0 0 1 2-2z"/></svg>
      <span>317-4821 Ostrander rd.<br>Pike hollow plaza</span>
    </div>
    <div class="contact">
      <svg width="13" height="13" viewBox="0 0 14 14" fill="none" stroke="#fff" stroke-width="1.2"><circle cx="7" cy="7" r="6"/><path d="M4.5 4c.5 2.8 2.2 4.7 5 5.5l.8-1.2-1.5-.9-.6.6c-1-.5-1.7-1.2-2.2-2.2l.6-.6-.9-1.5z"/></svg>
      <span>555 206 3379 (call or text)</span>
    </div>
    <div class="contact">
      <svg width="13" height="13" viewBox="0 0 14 14" fill="none" stroke="#fff" stroke-width="1.2"><circle cx="7" cy="7" r="6"/><rect x="4" y="6" width="6" height="4"/><path d="M5 6V4h4v2"/></svg>
      <span>555-206-3381</span>
    </div>
  </footer>
</section>

</body>
</html>
```